Business Card Design For A Cajun Seafood Restaurant

We are opening a cajun seafood restaurant in a week. We mainly serve cajun seafood which is orginally from Louisiana. We want design on both sides of a business card. I have menu on the website. You can go to www.reednkettle.example to check out our menu.

Restaurant name: Reed N' Kettle
Phone: +1 (555) 304-7712
Address: 48206 Ludlow Row, #7, Bexmoor Flats, Ca90000
Email: reednkettle@mailbox.example
Website: www.reednkettle.example

Maybe add social media icons (facebook, instagram) if looks nice on the business card.
facebook.com/reednkettle
instagram.com/reednkettle or @reednkettle

Attached is the logo and other business card samples that I like.

```html
<!DOCTYPE html>
<html lang="en">
<head>
<meta charset="utf-8">
<title>Reed N' Kettle – Business Card</title>
<link href="https://fonts.googleapis.com/css2?family=Roboto:wght@400;500;700&display=swap" rel="stylesheet">
<style>
  :root {
    --page: #e6e6e4;
    --card-white: #f7f7f5;
    --sunflower: #f2c418;
    --sunflower-deep: #e0ad0c;
    --pepper: #dd6128;
    --ink: #1c1a18;
    --ink-soft: #3a3835;
    --crab: #e3672c;
  }
  * { box-sizing: border-box; margin: 0; padding: 0; }
  html, body { width: 1200px; height: 576px; overflow: hidden; }
  body {
    background: var(--page);
    font-family: 'Roboto', Arial, sans-serif;
    position: relative;
  }
  .card {
    position: absolute;
    top: 139px;
    width: 484px;
    height: 293px;
    border-radius: 6px;
    overflow: hidden;
  }

  /* Front */
  .card--front {
    left: 82px;
    background: linear-gradient(135deg, var(--sunflower) 0%, #f0bd14 50%, var(--sunflower-deep) 100%);
  }
  .mascot {
    position: absolute;
    left: 190px;
    top: 57px;
    width: 120px;
    height: 110px;
    border-radius: 50%;
    background: radial-gradient(circle at 50% 45%, #ec7a3a 0%, var(--crab) 60%, rgba(227,103,44,0.0) 100%);
  }
  .front-name {
    position: absolute;
    left: 0;
    right: 0;
    top: 172px;
    text-align: center;
    font-weight: 700;
    font-size: 34px;
    letter-spacing: 0.5px;
    color: var(--ink);
  }

  /* Back */
  .card--back {
    left: 602px;
    background: var(--card-white);
  }
  .wave { position: absolute; left: 0; top: 0; width: 484px; height: 293px; }
  .person { position: absolute; left: 30px; top: 34px; }
  .person-name { font-weight: 500; font-size: 21px; color: var(--ink); line-height: 1.2; }
  .person-role { font-size: 11.5px; color: var(--ink-soft); margin-top: 2px; }
  .brand-name {
    position: absolute;
    right: 30px;
    top: 52px;
    font-weight: 700;
    font-size: 23px;
    color: var(--ink);
    letter-spacing: 0.3px;
  }
  .address {
    position: absolute;
    left: 30px;
    top: 142px;
    font-size: 13px;
    line-height: 18px;
    color: var(--ink-soft);
  }
  .social {
    position: absolute;
    left: 30px;
    top: 183px;
    list-style: none;
    font-size: 13px;
    line-height: 19px;
    color: var(--ink-soft);
  }
  .social li { display: flex; align-items: center; gap: 8px; }
  .social-mark { width: 10px; height: 10px; border-radius: 2px; display: inline-block; }
  .social-mark--blue { background: #3b5998; }
  .social-mark--brown { background: #8a5a3c; }
  .contact {
    position: absolute;
    right: 22px;
    top: 214px;
    list-style: none;
    font-size: 12.5px;
    line-height: 18px;
    color: #fff;
    text-align: right;
  }
  .contact li { display: flex; align-items: center; justify-content: flex-end; gap: 7px; }
  .contact svg { width: 11px; height: 11px; flex: none; }
</style>
</head>
<body>
  <section class="card card--front">
    <div class="mascot" role="img" aria-label="Cartoon crab mascot holding an ear of corn"></div>
    <div class="front-name">Reed N' Kettle</div>
  </section>

  <section class="card card--back">
    <svg class="wave" viewBox="0 0 484 293" aria-hidden="true">
      <path d="M0 266 C 120 300, 250 255, 340 205 S 445 160 484 157 L484 293 L0 293 Z" fill="var(--pepper)"/>
      <path d="M0 226 C 120 272, 250 222, 340 180 S 445 144 484 140 L484 150 C 435 152, 385 176, 332 207 S 120 292 0 250 Z" fill="var(--sunflower)"/>
      <path d="M0 242 C 110 262, 220 250, 300 228" fill="none" stroke="var(--sunflower)" stroke-width="2"/>
    </svg>

    <div class="person">
      <div class="person-name">Dana Whitfield</div>
      <div class="person-role">Director</div>
    </div>
    <div class="brand-name">Reed N' Kettle</div>

    <address class="address" style="font-style:normal">
      48206 Ludlow Row, #7,<br>Bexmoor Flats, Ca90000
    </address>

    <ul class="social">
      <li><span class="social-mark social-mark--blue"></span>@reednkettle</li>
      <li><span class="social-mark social-mark--brown"></span>/reednkettle</li>
    </ul>

    <ul class="contact">
      <li>+1 (555) 304-7712
        <svg viewBox="0 0 12 12"><path d="M3 1 L5 3.5 L4 4.8 C4.6 6 5.9 7.4 7.2 8 L8.5 7 L11 9 L9.8 11 C5.5 10.7 1.3 6.5 1 2.2 Z" fill="#fff"/></svg>
      </li>
      <li>www.reednkettle.example
        <svg viewBox="0 0 12 12"><circle cx="6" cy="6" r="5" fill="none" stroke="#fff" stroke-width="1.2"/><ellipse cx="6" cy="6" rx="2.2" ry="5" fill="none" stroke="#fff" stroke-width="1"/><line x1="1" y1="6" x2="11" y2="6" stroke="#fff" stroke-width="1"/></svg>
      </li>
      <li>reednkettle@mailbox.example
        <svg viewBox="0 0 12 12"><rect x="1" y="2.5" width="10" height="7" fill="#fff"/><path d="M1 2.5 L6 6.5 L11 2.5" fill="none" stroke="var(--pepper)" stroke-width="1"/></svg>
      </li>
    </ul>
  </section>
</body>
</html>
```